Harbourline Electrical Solutions

On one side. LOGO (underneath:) Commercial Industrial Residential

- NAME & CONTACT DETAILS

Marcus T. Hollings
Project Manager

(Cell icon) (441) 555-0187
(Email icon) hlelectricalsolutions@mailvento.com
(Facebook & Instagram icons )@hlelectricalsolutions

Other side: LOGO - underneath ELECTRICAL CONSTRUCTION & MAINTENANCE . LED LIGHTING & AUTOMATION . LIFE SAFETY SYSTEMS (FIRE ALARM / SECURITY) . DATA & COMMUNICATION

```html
<!DOCTYPE html>
<html lang="en">
<head>
<meta charset="utf-8">
<title>Harbourline Electrical Solutions – Business Card</title>
<link rel="stylesheet" href="https://fonts.googleapis.com/css2?family=Montserrat:wght@300;400;500;600;700&display=swap">
<style>
  :root {
    --backdrop: #262628;
    --teal: #10566b;
    --teal-deep: #0b4557;
    --teal-text: #17586e;
    --ink: #222;
    --ink-soft: #3a3a3a;
    --paper: #ffffff;
    --pale: #e9f0f2;
  }
  * { margin: 0; padding: 0; box-sizing: border-box; }
  html, body {
    width: 1200px; height: 1200px; overflow: hidden;
    background: var(--backdrop);
    font-family: "Montserrat", sans-serif;
  }
  .card {
    position: absolute; left: 286px; width: 612px; height: 367px;
  }
  .card--front { top: 217px; background: var(--teal); }
  .card--back { top: 630px; background: var(--paper); }

  .wordmark {
    position: absolute; display: flex; align-items: center; gap: 12px;
    font-weight: 600; text-transform: uppercase; letter-spacing: 3px; line-height: 1.15;
  }
  .wordmark__mark { width: 14px; height: 14px; }
  .card--front .wordmark {
    left: 0; right: 0; top: 126px; justify-content: center;
    color: var(--teal-deep); font-size: 22px;
  }
  .card--front .wordmark__mark { background: var(--teal-deep); }
  .card--back .wordmark {
    right: 50px; top: 38px; color: var(--teal-text); font-size: 17px;
  }
  .card--back .wordmark__mark { background: var(--teal-text); }

  .services {
    position: absolute; left: 71px; right: 60px; top: 310px;
    color: var(--pale); font-weight: 300; font-size: 11.3px; line-height: 17px;
  }
  .tagline {
    position: absolute; right: 49px; top: 111px;
    font-size: 9.6px; font-weight: 500; letter-spacing: 2.4px; color: var(--ink);
  }
  .tagline .sep { color: var(--teal-text); padding: 0 5px; }

  .contact-person { position: absolute; left: 46px; top: 243px; }
  .contact-person__name { color: var(--teal-text); font-weight: 700; font-size: 17px; }
  .contact-person__role { color: var(--ink-soft); font-size: 11.5px; font-weight: 500; margin-top: 1px; }
  .contact-person__rule { width: 49px; height: 2px; background: var(--teal-text); margin-top: 9px; }

  .contact-line {
    position: absolute; left: 46px; display: flex; align-items: center; gap: 4px;
    font-size: 12px; color: var(--ink-soft); font-weight: 500;
  }
  .contact-line svg { width: 13px; height: 13px; }
  .contact-line--phone { top: 300px; }
  .contact-line--email { top: 319px; }
  .contact-line--social { left: auto; right: 51px; top: 319px; gap: 6px; }
  .social-dot { width: 12px; height: 12px; border: 1.2px solid var(--teal-text); border-radius: 50%; }
</style>
</head>
<body>
  <section class="card card--front">
    <div class="wordmark"><span class="wordmark__mark"></span><span>Harbourline<br>Electrical<br>Solutions</span></div>
    <p class="services">ELECTRICAL CONSTRUCTION &amp; MAINTENANCE • LED LIGHTING &amp; AUTOMATION • LIFE SAFETY SYSTEMS (FIRE ALARM / SECURITY) • DATA &amp; COMMUNICATION</p>
  </section>

  <section class="card card--back">
    <div class="wordmark"><span class="wordmark__mark"></span><span>Harbourline<br>Electrical<br>Solutions</span></div>
    <p class="tagline">COMMERCIAL<span class="sep">|</span>INDUSTRIAL<span class="sep">|</span>RESIDENTIAL</p>

    <div class="contact-person">
      <h1 class="contact-person__name">MARCUS T. HOLLINGS</h1>
      <p class="contact-person__role">Project Manager</p>
      <div class="contact-person__rule"></div>
    </div>

    <p class="contact-line contact-line--phone">
      <svg viewBox="0 0 14 14" aria-hidden="true"><circle cx="7" cy="7" r="6.2" fill="none" stroke="#17586e" stroke-width="1"/><path d="M4.6 3.8l1.2-.2.6 1.5-.8.6c.4.9 1 1.5 1.9 1.9l.6-.8 1.5.6-.2 1.2c-2.7.2-5-2.1-4.8-4.8z" fill="#17586e"/></svg>
      (441) 555-0187
    </p>
    <p class="contact-line contact-line--email">
      <svg viewBox="0 0 14 14" aria-hidden="true"><circle cx="7" cy="7" r="6.2" fill="none" stroke="#17586e" stroke-width="1"/><rect x="3.8" y="4.8" width="6.4" height="4.4" fill="none" stroke="#17586e" stroke-width="0.9"/><path d="M3.8 4.8L7 7.4l3.2-2.6" fill="none" stroke="#17586e" stroke-width="0.9"/></svg>
      hlelectricalsolutions@mailvento.com
    </p>
    <p class="contact-line contact-line--social">
      <span class="social-dot"></span>
      @hlelectricalsolutions
    </p>
  </section>
</body>
</html>
```